FinTech company looking to revamp and expand client-facing interface for our financial models

Pellworth Engines currently has a very simple website that allows clients to interact with our financial models. We are looking to completely redesign the current site and add several extra pages to provide extra functionality. We want the design to have a modern, slick feel, that will work on both a desktop or a tablet. It should be straightforward for clients to move between different pages at any time, and clear from the layout how to interact with the more advanced features. We have included screenshots of existing pages in the attached design brief, as well as sketches of the functionality required by the new pages, but can't provide a direct link to the current site.
Target Market(s)
Professional investors that will be paying to access the interface
Industry/Entity Type
Finance
Number of Pages Required
4 page
Colors
Designer to choose colors to be used in the design.
Look and feel
Each slider illustrates characteristics of the customer's brand and the style your logo design should communicate.

```html
<!DOCTYPE html>
<html lang="en">
<head>
<meta charset="utf-8">
<title>Brisqal – Backtest</title>
<link href="https://fonts.googleapis.com/css2?family=Open+Sans:wght@400;600;700&family=Roboto+Condensed:wght@400;500&display=swap" rel="stylesheet">
<style>
:root{
  --navy:#0b3566;
  --teal:#087a6c;
  --ink:#1d1d1d;
  --bg:#e7e7e7;
  --panel:#ffffff;
  --row-alt:#f0f0f0;
  --line:#dcdcdc;
  --head-gray:#6b6b6b;
  --black:#1a1a1a;
}
*{box-sizing:border-box;margin:0;padding:0}
html,body{width:1200px;height:1122px;overflow:hidden;background:#fff}
.stage{position:absolute;left:0;top:0;width:1300px;height:1215px;transform:scale(.92308);transform-origin:0 0;font-family:"Open Sans",sans-serif;color:var(--ink)}
.abs{position:absolute}
.frame{left:15px;top:15px;width:1270px;height:1185px;background:var(--bg)}
.topnav{left:15px;top:15px;width:1270px;height:60px;background:var(--panel);display:flex;font-weight:700;font-size:15px}
.topnav > div{display:flex;align-items:center;justify-content:center;border-right:1px solid var(--line);height:60px;flex:none}
.brand{width:180px;font-size:19px}
.tf{width:90px}
.gap{width:135px}
.topnav > .tail{flex:1;border-right:none}
.nav-item{gap:8px;font-size:13px}
.nav-item svg{width:24px;height:24px}
.nav-item.active{background:var(--navy);color:#fff;border-right:none}
.modecard{left:105px;top:115px;width:1160px;height:90px;background:#f2f2f2;box-shadow:0 2px 6px rgba(0,0,0,.12)}
.tab{top:115px;height:42px;width:155px;display:flex;align-items:center;justify-content:center;font-size:14px;font-weight:600}
.tab.one{left:258px;background:#fff}
.tab.two{left:417px;background:var(--navy);color:#fff}
.chartcard{left:780px;top:200px;width:485px;height:340px;background:#fff;box-shadow:0 2px 6px rgba(0,0,0,.1)}
.options{left:800px;top:310px;width:50px;height:250px;background:#fff;box-shadow:2px 2px 6px rgba(0,0,0,.15)}
.options span{position:absolute;left:10px;top:168px;transform:rotate(-90deg);transform-origin:left top;font-weight:700;font-size:17px;letter-spacing:1px}
.export{left:1175px;top:592px;display:flex;align-items:center;gap:8px;color:var(--navy);font-weight:700;font-size:17px}
.table{font-family:"Roboto Condensed",sans-serif;font-size:18px;box-shadow:0 2px 6px rgba(0,0,0,.12)}
.row{display:flex;height:70px}
.rows .row:nth-child(even){background:var(--row-alt)}
.rows .row:nth-child(odd){background:#fff}
.cell{width:180px;display:flex;align-items:center;justify-content:center;border-right:1px solid #e4e4e4}
.thead{display:flex;height:70px;background:var(--black);color:#fff;font-weight:500;font-size:19px}
.thead .cell{border-right:1px solid #444}
.scroll{position:absolute;width:40px;background:#f3f3f3}
.scroll i{position:absolute;left:10px;width:20px;border:1px solid #999;border-radius:10px;background:#fff}
.scroll b{position:absolute;left:11px;width:18px;background:#8b8b8b;border-radius:9px}
.modal{left:15px;top:155px;width:785px;height:560px;background:#fff;box-shadow:0 3px 12px rgba(0,0,0,.25)}
.models{left:15px;top:15px;width:370px;height:530px;border:1px solid var(--line)}
.search{position:absolute;left:16px;top:10px;width:182px;height:31px;border:1px solid #bbb;border-radius:3px;padding-left:13px;font-size:16px;line-height:29px}
.select-btn{position:absolute;left:207px;top:10px;width:106px;height:30px;background:var(--teal);color:#fff;font-weight:600;font-size:16px;display:flex;align-items:center;justify-content:center;border-radius:2px}
.model-list{position:absolute;left:0;top:50px;width:330px}
.model{height:49.3px;border-top:1px solid var(--line);padding-left:20px;display:flex;align-items:center;font-weight:700;font-size:17px}
.model.active{background:var(--teal);color:#fff}
.add-btn{position:absolute;left:87px;top:470px;width:195px;height:40px;background:var(--navy);color:#fff;border-radius:3px;display:flex;align-items:center;justify-content:center;gap:12px;font-weight:700;font-size:13px}
.params{left:400px;top:15px;width:370px;height:530px;border:1px solid var(--line)}
.params-head{height:50px;background:var(--head-gray);color:#fff;font-weight:700;font-size:17px;display:flex;align-items:center;justify-content:center}
.param{height:50px;border-bottom:1px solid var(--line);display:flex;align-items:center;padding-left:17px;font-weight:700;font-size:16px}
.param label{width:97px}
.param span{width:240px;height:30px;border:1px solid #bbb;border-radius:3px;padding-left:12px;line-height:28px;font-weight:400;font-size:16px;box-shadow:inset 0 1px 2px rgba(0,0,0,.1)}
.run{position:absolute;left:108px;top:465px;width:153px;height:48px;background:var(--navy);color:#fff;font-weight:600;font-size:16px;display:flex;align-items:center;justify-content:center;border-radius:2px}
</style>
</head>
<body>
<div class="stage">
  <div class="abs frame"></div>

  <nav class="abs topnav">
    <div class="brand">BRISQAL</div>
    <div class="tf">250D</div><div class="tf">83D</div><div class="tf">42D</div>
    <div class="gap"></div>
    <div class="nav-item" style="width:140px"><svg viewBox="0 0 24 24"><path d="M3 11 12 3l9 8M6 9v12h5v-6h2v6h5V9" fill="none" stroke="#111" stroke-width="2.4"/></svg>MODELS</div>
    <div class="nav-item" style="width:178px"><svg viewBox="0 0 24 24"><g fill="#111"><circle cx="12" cy="12" r="3"/><circle cx="12" cy="3" r="1.6"/><circle cx="12" cy="21" r="1.6"/><circle cx="3" cy="12" r="1.6"/><circle cx="21" cy="12" r="1.6"/><circle cx="5.6" cy="5.6" r="1.6"/><circle cx="18.4" cy="18.4" r="1.6"/><circle cx="5.6" cy="18.4" r="1.6"/><circle cx="18.4" cy="5.6" r="1.6"/><circle cx="12" cy="7.5" r="1.1"/><circle cx="12" cy="16.5" r="1.1"/><circle cx="7.5" cy="12" r="1.1"/><circle cx="16.5" cy="12" r="1.1"/></g></svg>SENSITIVITIES</div>
    <div class="nav-item" style="width:160px"><svg viewBox="0 0 24 24"><g fill="none" stroke="#111" stroke-width="2"><circle cx="6.5" cy="6.5" r="4"/><circle cx="17.5" cy="6.5" r="4"/><circle cx="6.5" cy="17.5" r="4"/><circle cx="17.5" cy="17.5" r="4"/></g></svg>PORTFOLIO</div>
    <div class="nav-item active" style="width:152px"><svg viewBox="0 0 24 24"><g fill="none" stroke="#fff" stroke-width="1.8"><rect x="2" y="4" width="20" height="16"/><path d="M5 16l4-5 3 3 4-6 3 4"/></g></svg>BACKTEST</div>
    <div class="tail"></div>
  </nav>

  <div class="abs modecard"></div>
  <div class="abs tab one">Mode 1</div>
  <div class="abs tab two">Mode 2</div>

  <div class="abs chartcard">
    <svg width="485" height="340" viewBox="780 200 485 340">
      <g stroke="#ececec"><line x1="780" y1="263" x2="1112" y2="263"/><line x1="780" y1="300" x2="1112" y2="300"/><line x1="780" y1="337" x2="1112" y2="337"/><line x1="780" y1="374" x2="1112" y2="374"/><line x1="780" y1="411" x2="1112" y2="411"/></g>
      <line x1="780" y1="449" x2="1112" y2="449" stroke="#999"/>
      <line x1="800" y1="266" x2="1030" y2="267" stroke="#c8c43a" stroke-width="7" stroke-dasharray="6 3"/>
      <line x1="800" y1="263" x2="1064" y2="263" stroke="#4b7fc4" stroke-width="6" stroke-dasharray="7 2" stroke-linecap="round"/>
      <circle cx="1036" cy="446" r="4" fill="#5aa33a"/><circle cx="1044" cy="446" r="4" fill="#5aa33a"/>
      <g font-family="Open Sans,sans-serif" font-size="12" fill="#555"><text x="891" y="476">May 2019</text><text x="1036" y="476">Jul 2019</text><text x="1166" y="265" font-family="serif">Names</text></g>
      <g><circle cx="1150" cy="261" r="3.5" fill="#9cc3e6"/><circle cx="1150" cy="280" r="3.5" fill="#f5b27a"/><circle cx="1150" cy="299" r="3.5" fill="#3a9b3a"/><circle cx="1150" cy="318" r="3.5" fill="#e27b7b"/><circle cx="1150" cy="336" r="3.5" fill="#c5a6de"/><circle cx="1150" cy="355" r="3.5" fill="#b79a90"/><circle cx="1150" cy="373" r="3.5" fill="#eab5d8"/><circle cx="1150" cy="392" r="3.5" fill="#bdbdbd"/><circle cx="1150" cy="410" r="3.5" fill="#c8c43a"/><circle cx="1150" cy="429" r="3.5" fill="#8fd6e6"/><circle cx="1150" cy="448" r="3.5" fill="#2f5fa8"/></g>
    </svg>
  </div>

  <div class="abs options"><span>OPTIONS</span></div>
  <svg class="abs" style="left:836px;top:421px" width="28" height="28" viewBox="0 0 28 28"><circle cx="14" cy="14" r="12" fill="var(--navy)" stroke="#fff" stroke-width="2"/><path d="M20 14H8m5-5-5 5 5 5" fill="none" stroke="#fff" stroke-width="2.4"/></svg>

  <div class="abs export"><svg width="26" height="24" viewBox="0 0 26 24"><path d="M12 4H3v18h18v-8" fill="none" stroke="var(--navy)" stroke-width="2.4"/><path d="M9 16c1-6 5-9 12-9m-4-5 5 5-5 5" fill="none" stroke="var(--navy)" stroke-width="2.4"/></svg>Export</div>

  <div class="abs table" style="left:105px;top:700px;width:400px;height:420px;background:#fff">
    <div class="rows">
      <div class="row"><div class="cell">Stat 1</div><div class="cell">0.5</div></div>
      <div class="row"><div class="cell">Stat 2</div><div class="cell">-3</div></div>
      <div class="row"><div class="cell">Stat 3</div><div class="cell">30%</div></div>
      <div class="row"><div class="cell">Stat 4</div><div class="cell">0.5</div></div>
      <div class="row"><div class="cell">Stat 5</div><div class="cell">-3</div></div>
      <div class="row"><div class="cell">Stat 6</div><div class="cell">30%</div></div>
    </div>
    <div class="scroll" style="left:360px;top:0;height:420px"><i style="top:25px;height:370px"></i><b style="top:26px;height:74px"></b></div>
  </div>

  <div class="abs table" style="left:545px;top:630px;width:720px;height:490px;background:#fff">
    <div class="thead"><div class="cell">Open</div><div class="cell">Close</div><div class="cell">Size</div><div class="cell" style="border:none">Return</div></div>
    <div class="rows">
      <div class="row"><div class="cell">2018-04-05</div><div class="cell">2018-04-07</div><div class="cell">13</div><div class="cell">5%</div></div>
      <div class="row"><div class="cell">2018-04-05</div><div class="cell">2018-04-07</div><div class="cell">12</div><div class="cell">7%</div></div>
      <div class="row"><div class="cell">2018-04-05</div><div class="cell">2018-04-07</div><div class="cell">15</div><div class="cell">6%</div></div>
      <div class="row"><div class="cell">2018-04-05</div><div class="cell">2018-04-07</div><div class="cell">16</div><div class="cell">9%</div></div>
      <div class="row"><div class="cell">2018-04-05</div><div class="cell">2018-04-07</div><div class="cell">12</div><div class="cell">8%</div></div>
      <div class="row"><div class="cell">2018-04-05</div><div class="cell">2018-04-07</div><div class="cell">19</div><div class="cell">6%</div></div>
    </div>
    <div class="scroll" style="left:680px;top:70px;height:420px"><i style="top:25px;height:370px"></i><b style="top:26px;height:74px"></b></div>
  </div>

  <div class="abs modal">
    <div class="abs models">
      <div class="search">Model name</div>
      <div class="select-btn">Select</div>
      <div class="model-list">
        <div class="model">Model 1</div><div class="model">Model 2</div>
        <div class="model active">Model 3</div><div class="model">Model 4</div>
        <div class="model">Model 5</div><div class="model">Model 6</div>
        <div class="model">Model 7</div><div class="model">Model 8</div>
      </div>
      <div class="scroll" style="left:330px;top:50px;height:400px"><i style="top:25px;height:350px"></i><b style="top:26px;height:72px"></b></div>
      <div class="add-btn"><svg width="22" height="22" viewBox="0 0 22 22"><circle cx="11" cy="11" r="9.5" fill="none" stroke="#fff" stroke-width="1.6"/><path d="M11 6v10M6 11h10" stroke="#fff" stroke-width="1.6"/></svg>ADD A MODEL</div>
    </div>
    <div class="abs params">
      <div class="params-head">Parameters:</div>
      <div class="param"><label>Entry:</label><span>0.5</span></div>
      <div class="param"><label>Exit:</label><span>-0.3</span></div>
      <div class="param"><label>Lookback:</label><span>5</span></div>
      <div class="param"><label>Entry:</label><span>0.5</span></div>
      <div class="param"><label>Exit:</label><span>-0.3</span></div>
      <div class="param"><label>Lookback:</label><span>5</span></div>
      <div class="param"><label>Entry:</label><span>0.5</span></div>
      <div class="param"><label>Exit:</label><span>-0.3</span></div>
      <div class="run">RUN</div>
    </div>
  </div>

  <svg class="abs" style="left:150px;top:350px" width="30" height="38" viewBox="0 0 30 38"><path d="M9 3c1.5 0 2.5 1 2.5 2.5V16l1-.5c1.5-.5 2.5 0 3 1 1.5-.7 2.7 0 3.2 1 1.5-.6 2.8.2 3.1 1.4 1.5-.4 2.7.6 2.7 2V28c0 4-3 7-7 7h-3c-3 0-5-1.5-6.5-4L3 23c-.8-1.4.8-3 2.3-2.2L6.5 22V5.5C6.5 4 7.5 3 9 3z" fill="#fff" stroke="#000" stroke-width="1.6"/><path d="M12.5 16v6m3.5-5v5m3.5-4v4" stroke="#000" stroke-width="1.3"/></svg>
</div>
</body>
</html>
```